Company Mission & Values Poster

I'd like an A2 Portrait Poster displaying our company's Mission & Values.
See our website for our logo, fonts, mission & values.
https://valdintor.com.au/

Our Mission: Creating homes for abundant life
Values: Love, Thinking, Team, Zoe.

Some ideas to consider:
Mission as the Headline then
A logo for each of the 4 Values and the words

Target Market(s)

Myself & my team

Industry/Entity Type

Real Estate

Font styles to use
Other font styles liked:
• Company fonts as seen on our website

```html
<!DOCTYPE html>
<html lang="en">
<head>
<meta charset="utf-8">
<title>Valdintor — Mission &amp; Values</title>
<link rel="stylesheet" href="https://fonts.googleapis.com/css2?family=Playfair+Display:wght@400;600;700&family=Fraunces:opsz,wght@9..144,600&display=swap">
<style>
  :root {
    --ink: #ffffff;
    --rule: rgba(255,255,255,0.85);
    --canopy: #5e5c52;
    --sky: #7d9190;
    --foliage: #3f5a4c;
    --terrace: #46524f;
    --floor: #3b4644;
  }
  * { margin: 0; padding: 0; box-sizing: border-box; }
  html, body { width: 849px; height: 1200px; overflow: hidden; background: var(--floor); }
  .poster {
    position: relative;
    width: 849px;
    height: 1200px;
    overflow: hidden;
    color: var(--ink);
  }
  .backdrop {
    position: absolute; inset: 0;
    background:
      linear-gradient(160deg, var(--canopy) 0%, #6a6a5e 14%, transparent 24%),
      radial-gradient(ellipse 60% 30% at 25% 45%, rgba(70,95,70,0.9), transparent 70%),
      radial-gradient(ellipse 40% 25% at 80% 40%, rgba(120,140,130,0.6), transparent 70%),
      linear-gradient(180deg, #6a6c62 0%, var(--sky) 26%, var(--foliage) 48%, var(--terrace) 70%, var(--floor) 100%);
  }
  .backdrop::after {
    content: ""; position: absolute; inset: 0;
    background: rgba(20,30,28,0.22);
  }
  .headline { position: absolute; left: 0; top: 0; width: 849px; height: 360px; }
  .headline text {
    font-family: "Playfair Display", serif;
    font-weight: 600;
    fill: var(--ink);
  }
  .value {
    position: absolute; left: 0; width: 849px;
    text-align: center;
  }
  .value-head {
    position: relative; height: 40px;
  }
  .value-head svg { position: absolute; left: 0; top: 0; }
  .value-title {
    position: relative;
    font-family: "Playfair Display", serif;
    font-weight: 700;
    font-size: 36px;
    line-height: 40px;
    letter-spacing: 0.5px;
  }
  .value-text {
    font-family: "Fraunces", serif;
    font-weight: 600;
    font-size: 14.5px;
    line-height: 27.3px;
    letter-spacing: 0.3px;
    margin-top: 2px;
  }
  .wordmark {
    position: absolute; left: 0; top: 1066px; width: 849px;
    display: flex; justify-content: center; align-items: center; gap: 22px;
  }
  .wordmark-dot { width: 20px; height: 20px; border-radius: 50%; background: var(--ink); }
  .wordmark-name {
    font-family: "Playfair Display", serif;
    font-weight: 400;
    font-size: 46px;
    letter-spacing: 7px;
    line-height: 50px;
  }
</style>
</head>
<body>
<main class="poster">
  <div class="backdrop" role="img" aria-label="Photograph of a shaded outdoor terrace with woven dining chairs and a stone table, lush garden trees and a harbour view under a curved concrete canopy"></div>

  <svg class="headline" viewBox="0 0 849 360" aria-label="Creating homes for abundant life">
    <text x="141" y="159" font-size="94" textLength="566" lengthAdjust="spacingAndGlyphs">CREATING</text>
    <text x="141" y="294" font-size="150" textLength="566" lengthAdjust="spacingAndGlyphs">HOMES</text>
    <text x="145" y="350" font-size="54" textLength="558" lengthAdjust="spacingAndGlyphs">FOR ABUNDANT LIFE</text>
  </svg>

  <section class="value" style="top:429px">
    <div class="value-head">
      <svg width="849" height="40" viewBox="0 0 849 40"><g stroke="var(--rule)" stroke-width="1" fill="var(--ink)"><line x1="139" y1="20" x2="363" y2="20"/><circle cx="365" cy="20" r="2"/><circle cx="498" cy="20" r="2"/><line x1="502" y1="20" x2="722" y2="20"/></g></svg>
      <h2 class="value-title">LOVE</h2>
    </div>
    <p class="value-text">Our mission is founded in our love and respect for people –<br>those we develop for, those in our teams and those in the<br>communities we create and operate within.</p>
  </section>

  <section class="value" style="top:576px">
    <div class="value-head">
      <svg width="849" height="40" viewBox="0 0 849 40"><g stroke="var(--rule)" stroke-width="1" fill="var(--ink)"><line x1="139" y1="20" x2="314" y2="20"/><circle cx="318" cy="20" r="2"/><circle cx="534" cy="20" r="2"/><line x1="538" y1="20" x2="722" y2="20"/></g></svg>
      <h2 class="value-title">THINKING</h2>
    </div>
    <p class="value-text">We believe in the power of thinking. Our rigorous and creative<br>processes create beautifully considered solutions for our purchasers,<br>the communities we develop within and the environment.</p>
  </section>

  <section class="value" style="top:722px">
    <div class="value-head">
      <svg width="849" height="40" viewBox="0 0 849 40"><g stroke="var(--rule)" stroke-width="1" fill="var(--ink)"><line x1="139" y1="20" x2="360" y2="20"/><circle cx="364" cy="20" r="2"/><circle cx="498" cy="20" r="2"/><line x1="502" y1="20" x2="722" y2="20"/></g></svg>
      <h2 class="value-title">TEAM</h2>
    </div>
    <p class="value-text">Property development is a team sport. We surround ourselves<br>with the best designers and advisers. We strive to create an environment<br>that allows them to do their best work and love doing it.</p>
  </section>

  <section class="value" style="top:871px">
    <div class="value-head">
      <svg width="849" height="40" viewBox="0 0 849 40"><g stroke="var(--rule)" stroke-width="1" fill="var(--ink)"><line x1="139" y1="20" x2="362" y2="20"/><circle cx="364" cy="20" r="2"/><circle cx="498" cy="20" r="2"/><line x1="502" y1="20" x2="722" y2="20"/></g></svg>
      <h2 class="value-title">ZOE</h2>
    </div>
    <p class="value-text">Our mission is to create places for ‘Zoe’<br>the Greek word for abundant life. We do this through exquisite design,<br>quality construction and celebrating nature.</p>
  </section>

  <footer class="wordmark">
    <span class="wordmark-dot" aria-hidden="true"></span>
    <span class="wordmark-name">VALDINTOR</span>
  </footer>
</main>
</body>
</html>
```